Harborline Auto LLC

Car Dealer Customer Service
Address: 2874 Cresthaven Road, Larkhaven, QX 00462
web: www.harborlineautoxq.net
email: harborlineautoxq@mailnest.example
Phone: (555) 555-0148
Phone: (555) 555-0173

```html
<!DOCTYPE html>
<html lang="en">
<head>
<meta charset="utf-8">
<title>Harborline Auto – Business Card</title>
<link href="https://fonts.googleapis.com/css2?family=Montserrat:wght@400;500;700;800&display=swap" rel="stylesheet">
<style>
  :root {
    --brand-blue: #1b7db0;
    --brand-gold: #e9b040;
    --ink: #1a1a1a;
    --paper: #ffffff;
    --backdrop: #c9c9c9;
  }
  * { box-sizing: border-box; margin: 0; padding: 0; }
  html, body { width: 1200px; height: 813px; overflow: hidden; }
  body {
    background: var(--backdrop);
    font-family: "Montserrat", sans-serif;
    position: relative;
  }
  .card {
    position: absolute;
    width: 540px;
    height: 310px;
    border-radius: 20px;
    overflow: hidden;
    box-shadow: 0 10px 24px rgba(0,0,0,0.25);
  }
  .card--front { left: 40px; top: 252px; background: var(--paper); }
  .card--back {
    left: 620px; top: 252px;
    background: var(--brand-blue);
    border-bottom: 6px solid var(--brand-gold);
    display: flex; flex-direction: column; align-items: center; justify-content: center;
    gap: 22px;
  }
  .card__wave { position: absolute; inset: 0; }
  .brand {
    position: absolute;
    left: 20px; top: 60px; width: 220px;
    display: flex; flex-direction: column; align-items: center; gap: 14px;
  }
  .brand__mark {
    width: 62px; height: 62px; border-radius: 50%;
    background: var(--brand-blue);
  }
  .brand__name {
    color: var(--brand-blue);
    font-weight: 800;
    font-size: 24px;
    line-height: 1.1;
    letter-spacing: 1px;
    text-align: center;
  }
  .divider {
    position: absolute;
    left: 250px; top: 36px;
    width: 1.5px; height: 150px;
    background: var(--brand-blue);
  }
  .contact {
    position: absolute;
    left: 266px; top: 30px;
    color: var(--ink);
    font-size: 12.5px;
    line-height: 20px;
    font-weight: 500;
  }
  .contact__row { display: flex; align-items: center; gap: 6px; white-space: nowrap; }
  .contact__icon { width: 12px; height: 12px; flex: none; fill: var(--brand-blue); }
  .contact__web-name { color: var(--brand-blue); }
  .back__mark {
    width: 110px; height: 110px; border-radius: 50%;
    background: var(--paper);
  }
  .back__name {
    color: var(--paper);
    font-weight: 800;
    font-size: 38px;
    letter-spacing: 2px;
  }
</style>
</head>
<body>

  <section class="card card--front" aria-label="Business card front">
    <svg class="card__wave" viewBox="0 0 540 310" preserveAspectRatio="none" aria-hidden="true">
      <path d="M0 295 C180 290 330 250 430 215 C480 198 510 192 540 190 L540 310 L0 310 Z" fill="var(--brand-blue)"/>
      <path d="M0 287 C180 282 330 242 430 207 C480 190 510 184 540 182" fill="none" stroke="var(--brand-gold)" stroke-width="3"/>
    </svg>

    <div class="brand">
      <span class="brand__mark" aria-hidden="true"></span>
      <span class="brand__name">HARBORLINE<br>AUTO</span>
    </div>

    <span class="divider" aria-hidden="true"></span>

    <div class="contact">
      <p class="contact__row">Car Dealer Customer Service</p>
      <p class="contact__row">2874 Cresthaven Road,</p>
      <p class="contact__row">Larkhaven, QX 00462</p>
      <p class="contact__row">
        <svg class="contact__icon" viewBox="0 0 24 24" aria-hidden="true"><path d="M6.6 10.8a15 15 0 0 0 6.6 6.6l2.2-2.2c.3-.3.7-.4 1-.2 1.1.4 2.3.6 3.6.6.6 0 1 .4 1 1V20c0 .6-.4 1-1 1A17 17 0 0 1 3 4c0-.6.4-1 1-1h3.5c.6 0 1 .4 1 1 0 1.3.2 2.5.6 3.6.1.3 0 .7-.2 1z"/></svg>
        <span>(555) 555-0148</span>
      </p>
      <p class="contact__row">
        <svg class="contact__icon" viewBox="0 0 24 24" aria-hidden="true"><path d="M6.6 10.8a15 15 0 0 0 6.6 6.6l2.2-2.2c.3-.3.7-.4 1-.2 1.1.4 2.3.6 3.6.6.6 0 1 .4 1 1V20c0 .6-.4 1-1 1A17 17 0 0 1 3 4c0-.6.4-1 1-1h3.5c.6 0 1 .4 1 1 0 1.3.2 2.5.6 3.6.1.3 0 .7-.2 1z"/></svg>
        <span>(555) 555-0173</span>
      </p>
      <p class="contact__row">
        <svg class="contact__icon" viewBox="0 0 24 24" aria-hidden="true"><path d="M2 5h20v14H2z M2 5l10 8 10-8" /></svg>
        <span>harborlineautoxq@mailnest.example</span>
      </p>
      <p class="contact__row">
        <svg class="contact__icon" viewBox="0 0 24 24" aria-hidden="true"><circle cx="12" cy="12" r="10"/></svg>
        <span>www.<span class="contact__web-name">harborlineautoxq</span>.net</span>
      </p>
    </div>
  </section>

  <section class="card card--back" aria-label="Business card back">
    <span class="back__mark" aria-hidden="true"></span>
    <span class="back__name">HARBORLINE AUTO</span>
  </section>

</body>
</html>
```